US company marketing to law enforcement needs brochure design

We have created a new logo and now need to update our printed material. What we really need is a "style" or "template" for how our brochures will look in the future. Enclosed is the brochure draft with the old style and logo. Also enclosed is the new logo. As we are marketing to US law enforcement it is important the the brochure design is strong, powerful and that we are looking experienced and trustworthy. However, we also want to look modern in line with the logo update.

Target Market(s)

Law enforcement

Industry/Entity Type

Marketing

```html
<!DOCTYPE html>
<html lang="en">
<head>
<meta charset="utf-8">
<title>Steadfast Programs – Brochure Cover Spread</title>
<link href="https://fonts.googleapis.com/css2?family=Ubuntu:wght@400;500&display=swap" rel="stylesheet">
<style>
  :root {
    --navy: #1d386c;
    --sky: #8fb0e0;
    --grey: #8c8c8c;
    --paper: #ffffff;
    --backdrop: #e9e6e1;
    --fold: #d9d9d9;
    --photo-glow: #9a6a54;
    --photo-mid: #5e3628;
    --photo-dark: #1f100b;
  }
  html, body {
    margin: 0;
    width: 1200px;
    height: 868px;
    overflow: hidden;
    background: var(--backdrop);
    font-family: "Ubuntu", sans-serif;
  }
  .spread {
    position: absolute;
    left: 41px;
    top: 38px;
    width: 1396px;
    height: 989px;
    transform: scale(0.8);
    transform-origin: top left;
    display: flex;
    background: var(--paper);
  }
  .panel {
    position: relative;
    width: 698px;
    height: 989px;
    overflow: hidden;
  }
  .panel--back { border-right: 1px solid var(--fold); }
  .panel svg.shapes {
    position: absolute;
    inset: 0;
    width: 698px;
    height: 989px;
  }
  .brand {
    position: absolute;
    display: flex;
    align-items: center;
    gap: 24px;
  }
  .brand__dot {
    width: 84px;
    height: 84px;
    border-radius: 50%;
    background: var(--navy);
    flex: none;
  }
  .brand__name {
    font-weight: 500;
    font-size: 45px;
    letter-spacing: -0.5px;
    white-space: nowrap;
  }
  .panel--back .brand { left: 102px; top: 453px; }
  .panel--back .brand__name { color: var(--navy); }
  .panel--front .brand { left: 100px; top: 78px; }
  .panel--front .brand__name { color: var(--grey); }
  .services {
    position: absolute;
    left: 0;
    right: 0;
    top: 828px;
    text-align: center;
    color: var(--navy);
    font-size: 25px;
    line-height: 53px;
    margin: 0;
    padding: 0 0 0 20px;
    list-style: none;
  }
  .services li { white-space: nowrap; }
  .services .sep { margin: 0 17px; }
</style>
</head>
<body>
  <div class="spread">
    <section class="panel panel--back">
      <svg class="shapes" viewBox="0 0 698 989" aria-hidden="true">
        <path d="M280,0 L698,0 L698,58 Q560,8 280,0 Z" fill="var(--navy)"/>
        <path d="M0,930 Q190,985 420,989 L0,989 Z" fill="var(--navy)"/>
      </svg>
      <div class="brand">
        <span class="brand__dot"></span>
        <span class="brand__name">Steadfast Programs</span>
      </div>
    </section>

    <section class="panel panel--front">
      <svg class="shapes" viewBox="0 0 698 989">
        <defs>
          <radialGradient id="photoTone" cx="0.68" cy="0.48" r="0.7">
            <stop offset="0" stop-color="var(--photo-glow)"/>
            <stop offset="0.5" stop-color="var(--photo-mid)"/>
            <stop offset="1" stop-color="var(--photo-dark)"/>
          </radialGradient>
        </defs>
        <path d="M78,217 Q380,262 698,246 Q400,292 78,232 Z" fill="var(--sky)"/>
        <path d="M40,229 Q360,286 698,245 L698,250 Q360,298 40,255 Z" fill="var(--navy)"/>
        <path role="img" aria-label="Photograph of a wooden gavel resting on law books beside brass scales of justice"
              d="M0,247 Q380,300 698,245 L698,745 Q380,686 0,745 Z" fill="url(#photoTone)"/>
        <path d="M0,745 Q380,694 658,738 L658,760 Q400,712 0,745 Z" fill="var(--navy)"/>
        <path d="M120,716 Q420,712 622,760 L622,775 Q400,724 120,716 Z" fill="var(--sky)"/>
      </svg>
      <div class="brand">
        <span class="brand__dot"></span>
        <span class="brand__name">Steadfast Programs</span>
      </div>
      <ul class="services">
        <li>Pre Trial<span class="sep">•</span>Diversion<span class="sep">•</span>Deferred Prosecution</li>
        <li>Jail Alternative<span class="sep">•</span>Probation</li>
      </ul>
    </section>
  </div>
</body>
</html>
```